Request for Business Card Design

Hi. My name is Marlene, I am looking for a new business card design for my company, Quarrow Signal Instruments, LLC. I really like the design you did for Tarsel Venture and was hoping you could do something similar using our full logo and our mark. I am also open to any raised texture design using our mark. I have attached our full logo, which would need to be somewhere on the card, as well as the mark in both outline and full form, as well as our brand colors / guide. The card does not have to be white, as long as our logo and mark appear. I actually like darker colored business cards more, but am open to all options. If you are interested in working with me, please let me know. We would also take the business card design into letterhead design if you can do that.

```html
<!DOCTYPE html>
<html lang="en">
<head>
<meta charset="utf-8">
<title>Quarrow Signal Instruments — Business Card</title>
<link rel="stylesheet" href="https://fonts.googleapis.com/css2?family=Open+Sans:wght@400;600;700;800&display=swap">
<style>
  :root {
    --stage: #232324;
    --card: #3b3b3e;
    --card-deep: #333336;
    --card-shade: #2c2c2f;
    --ink: #ffffff;
    --ink-soft: #d9d9dc;
    --accent: #1a9bcf;
    --pattern-light: #8a8a8e;
    --pattern-dark: #2e2e31;
  }
  * { box-sizing: border-box; margin: 0; padding: 0; }
  html, body {
    width: 1200px; height: 780px; overflow: hidden;
    background: var(--stage);
    font-family: "Open Sans", Arial, sans-serif;
  }
  .stage {
    position: relative; width: 1200px; height: 780px;
    display: flex; justify-content: center; align-items: center; gap: 90px;
  }
  .card {
    position: relative; width: 370px; height: 640px;
    border-radius: 26px; overflow: hidden;
    background: var(--card);
    box-shadow: 0 18px 40px rgba(0,0,0,.55);
  }

  /* back */
  .card-back__pattern {
    position: absolute; inset: 0;
    background: linear-gradient(135deg, var(--pattern-light) 0%, #4a4a4e 28%, var(--card) 50%, var(--pattern-dark) 100%);
  }
  .card-back__brand {
    position: absolute; top: 36px; right: 34px;
    display: flex; align-items: center; gap: 10px;
  }
  .brand-dot {
    width: 18px; height: 18px; border-radius: 50%;
    background: var(--accent); flex: none;
  }
  .brand-name {
    color: var(--ink); font-weight: 700; letter-spacing: .06em;
    text-transform: uppercase; line-height: 1.1;
  }
  .card-back__brand .brand-name { font-size: 12px; }

  /* front */
  .card-front__layers { position: absolute; inset: 0; }
  .card-front__brand {
    position: absolute; top: 56px; left: 34px; right: 30px;
    display: flex; align-items: center; gap: 14px;
  }
  .card-front__brand .brand-dot { width: 34px; height: 34px; }
  .card-front__brand .brand-name { font-size: 17px; }
  .person {
    position: absolute; top: 196px; left: 0; right: 0; text-align: center;
  }
  .person__name {
    color: var(--accent); font-size: 44px; font-weight: 800; line-height: 1;
    letter-spacing: .01em;
  }
  .person__role {
    color: var(--ink); font-size: 15px; font-weight: 600; margin-top: 4px;
  }
  .contact-links { position: absolute; inset: 0; }
  .contact-list {
    position: absolute; top: 320px; left: 0; right: 0;
    list-style: none; text-align: center;
    color: var(--ink); font-size: 14.5px; line-height: 26px;
  }
  .address {
    position: absolute; top: 548px; left: 0; right: 0; text-align: center;
    color: var(--ink-soft); font-size: 14.5px; line-height: 22px;
  }
</style>
</head>
<body>
<main class="stage">

  <section class="card card-back" aria-label="Card back">
    <div class="card-back__pattern" role="img" aria-label="Raised repeating pattern of the company mark, fading from light silver to dark grey"></div>
    <div class="card-back__brand">
      <span class="brand-dot"></span>
      <span class="brand-name">Quarrow Signal Instruments</span>
    </div>
  </section>

  <section class="card card-front" aria-label="Card front">
    <svg class="card-front__layers" width="370" height="640" viewBox="0 0 370 640" aria-hidden="true">
      <defs>
        <linearGradient id="panelShade" x1="0" y1="0" x2="0" y2="1">
          <stop offset="0" stop-color="#2a2a2d" stop-opacity=".6"/>
          <stop offset="1" stop-color="#2a2a2d" stop-opacity="0"/>
        </linearGradient>
      </defs>
      <path d="M0 470 Q120 470 220 430 Q300 398 370 330 L370 640 L0 640 Z" fill="var(--card-deep)"/>
      <path d="M0 470 Q120 480 220 440 Q300 408 370 340 L370 352 Q300 420 220 452 Q120 492 0 484 Z" fill="url(#panelShade)"/>
      <path d="M0 520 Q160 520 260 470 Q330 436 370 400 L370 640 L0 640 Z" fill="var(--card-shade)" opacity=".55"/>

      <!-- contact icons -->
      <g class="contact-icons">
        <circle cx="130" cy="290" r="13" fill="var(--accent)"/>
        <rect x="123" y="285" width="14" height="10" fill="none" stroke="#fff" stroke-width="1.5"/>
        <path d="M123 285 L130 291 L137 285" fill="none" stroke="#fff" stroke-width="1.5"/>

        <circle cx="170" cy="290" r="13" fill="var(--accent)"/>
        <path d="M165 284 q-2 8 9 12 l2 -3 -3 -2 -2 2 q-4 -2 -5 -6 l2 -1 -1 -3 z" fill="#fff"/>

        <circle cx="210" cy="290" r="13" fill="var(--accent)"/>
        <rect x="203" y="287" width="14" height="8" rx="1" fill="#fff"/>
        <rect x="206" y="283" width="8" height="4" fill="#fff"/>

        <circle cx="250" cy="290" r="13" fill="var(--accent)"/>
        <circle cx="250" cy="290" r="7" fill="none" stroke="#fff" stroke-width="1.5"/>
        <path d="M243 290 H257 M250 283 Q246 290 250 297 M250 283 Q254 290 250 297" fill="none" stroke="#fff" stroke-width="1.2"/>
      </g>

      <!-- connectors -->
      <g fill="none" stroke="var(--accent)" stroke-width="1.6">
        <path d="M117 290 H34 V387 H60"/>
        <path d="M263 290 H340 V413 H318"/>
        <path d="M170 303 V312 H96 V335 H108"/>
        <path d="M210 303 V312 H292 V335 H280"/>
      </g>
      <g fill="var(--accent)">
        <path d="M66 387 L58 383 V391 Z"/>
        <path d="M312 413 L320 409 V417 Z"/>
        <path d="M114 335 L106 331 V339 Z"/>
        <path d="M274 335 L282 331 V339 Z"/>
      </g>

      <!-- location pin -->
      <circle cx="185" cy="526" r="13" fill="var(--accent)"/>
      <path d="M185 531 q-6 -6 -6 -10 a6 6 0 0 1 12 0 q0 4 -6 10 z" fill="#fff"/>
      <circle cx="185" cy="521" r="2.2" fill="var(--accent)"/>
    </svg>

    <div class="card-front__brand">
      <span class="brand-dot"></span>
      <span class="brand-name">Quarrow Signal Instruments</span>
    </div>

    <div class="person">
      <h1 class="person__name">Marlene</h1>
      <p class="person__role">Director</p>
    </div>

    <ul class="contact-list">
      <li>+001 303 555 0142</li>
      <li>+001 303 555 0187</li>
      <li>info@quarrowsignal.com</li>
      <li>www.quarrowsignal.com</li>
    </ul>

    <p class="address">1180 Harbor Ridge Avenue •<br>Ashford, CO 80999</p>
  </section>

</main>
</body>
</html>
```